Coastline Premier Retreats Business Card Design

Design a business card for Coastline Premier Retreats. Look at the website for colors and reference. Card should have logo, name, title, office number, mobile number, email, URL and a tagline like, "Luxury Hotel & Resort Email Marketing" (This might change).

https://www.coastlinepremierretreats.example

The rest I will leave up to your imagination.

Contact Information for Business Card

Logo, name, title, office number, mobile number, email, URL and a tagline like, "Luxury Hotel & Resort Email Marketing" (This might change).

```html
<!DOCTYPE html>
<html lang="en">
<head>
<meta charset="utf-8">
<title>Coastline Premier Retreats – Business Card</title>
<link href="https://fonts.googleapis.com/css2?family=Poppins:wght@400;600;700&display=swap" rel="stylesheet">
<style>
  :root{
    --bg:#2a2a2c;
    --card:#1b1c1e;
    --card-back-a:#202124;
    --card-back-b:#151618;
    --orange:#f57300;
    --white:#ffffff;
    --muted:#5a5b5f;
  }
  *{box-sizing:border-box;margin:0;padding:0}
  html,body{width:1200px;height:1108px;overflow:hidden}
  body{background:var(--bg);font-family:"Poppins",sans-serif;position:relative}
  .card{position:absolute;top:186px;width:420px;height:736px;border-radius:30px;overflow:hidden;box-shadow:0 20px 40px rgba(0,0,0,.45)}
  .card-front{left:130px;background:var(--card)}
  .card-back{left:650px;background:linear-gradient(150deg,var(--card-back-a),var(--card-back-b))}

  .brand{position:absolute;left:0;right:0;display:flex;align-items:center;justify-content:center;gap:12px;color:var(--white);font-weight:600;text-transform:uppercase;letter-spacing:.04em}
  .card-front .brand{top:110px;font-size:22px}
  .brand-mark{width:16px;height:16px;background:var(--orange);flex:none}

  .person{position:absolute;top:360px;left:0;right:0;text-align:center}
  .person-name{font-size:32px;font-weight:600;color:var(--white);text-transform:uppercase;letter-spacing:.02em;line-height:1.1}
  .person-title{font-size:19px;font-weight:400;color:var(--orange);text-transform:uppercase;letter-spacing:.03em;margin-top:2px}

  .icon-row{position:absolute;top:470px;left:34px;right:34px;display:flex;align-items:center;gap:10px}
  .icon-row .rule{flex:1;height:1px;background:var(--muted)}
  .icon{width:38px;height:38px;border-radius:6px;background:var(--orange);display:flex;align-items:center;justify-content:center}
  .icon svg{width:22px;height:22px}

  .contact{position:absolute;top:528px;left:0;right:0;text-align:center;color:var(--white);font-size:17px;line-height:1.45}
  .contact .phone{font-size:20px}

  .tagline-band{position:absolute;left:0;right:0;bottom:0;height:88px;background:var(--orange);display:flex;align-items:center;justify-content:center}
  .tagline{color:var(--white);font-weight:600;font-size:18px;text-transform:uppercase;letter-spacing:.02em}

  .back-texture{position:absolute;inset:0}
  .card-back .brand{top:50%;transform:translateY(-50%);font-size:22px}
</style>
</head>
<body>
  <section class="card card-front" aria-label="Business card front">
    <div class="brand"><span class="brand-mark"></span><span>Coastline Premier Retreats</span></div>

    <div class="person">
      <h1 class="person-name">Daniel Reyes</h1>
      <p class="person-title">Managing Director</p>
    </div>

    <div class="icon-row">
      <span class="rule"></span>
      <span class="icon" aria-label="Office phone">
        <svg viewBox="0 0 24 24" fill="#fff"><path d="M3 9c0-2 3-4 9-4s9 2 9 4v2h-4V9c-1-.6-3-1-5-1s-4 .4-5 1v2H3z"/><path d="M6 12h12l2 7H4z"/><circle cx="12" cy="15.5" r="2" fill="#f57300"/></svg>
      </span>
      <span class="icon" aria-label="Mobile phone">
        <svg viewBox="0 0 24 24" fill="none" stroke="#fff" stroke-width="2"><rect x="7" y="2.5" width="10" height="19" rx="2"/><circle cx="12" cy="18" r=".8" fill="#fff"/></svg>
      </span>
      <span class="icon" aria-label="Email">
        <svg viewBox="0 0 24 24" fill="none" stroke="#fff" stroke-width="2"><rect x="3" y="5.5" width="18" height="13" rx="1"/><path d="M3 6l9 7 9-7"/></svg>
      </span>
      <span class="icon" aria-label="Website">
        <svg viewBox="0 0 24 24" fill="none" stroke="#fff" stroke-width="1.8"><circle cx="12" cy="12" r="9"/><ellipse cx="12" cy="12" rx="4" ry="9"/><path d="M3 12h18"/></svg>
      </span>
      <span class="rule"></span>
    </div>

    <address class="contact" style="font-style:normal">
      <div class="phone">555.014.2000</div>
      <div class="phone">555.014.7380</div>
      <div>dreyes@coastlinepremierretreats.example</div>
      <div>www.coastlinepremierretreats.example</div>
    </address>

    <div class="tagline-band"><p class="tagline">Luxury Hotel &amp; Resort Email Marketing</p></div>
  </section>

  <section class="card card-back" aria-label="Business card back">
    <div class="back-texture" role="img" aria-label="Faint tone-on-tone repeating brand name pattern"></div>
    <div class="brand"><span class="brand-mark"></span><span>Coastline Premier Retreats</span></div>
  </section>
</body>
</html>
```